Meal Plan Website Needs New Pages Designed

Brightwick Supper Kits is an online, membership based program that delivers weekly meal programs (7 days worth of recipes plus shopping lists) carefully crafted by an expert team of meal planners. All recipes are created to comply with the following macronutrient ratio: 65% healthy fats, 25% lean protein, 10% good carbs.
All recipes are Paleo friendly and a great resource for those individuals who want to correctly implement this type of diet.

We are re-designing our website and need the following pages designed:

· Home page w/ logo
· How it works page
· Get Started! page
· Recipes Page template (these will be the pages on our site that will have recipes)
· Kitchen Essentials Training page (this will be a page with videos and tips + tricks, PDFs, etc)

So 5 total PSDs, 1 for each page.

Target audience: Men and women between the ages of 30 and 60 who want to:
· Eat healthy
· Lose weight
· Follow/Implement the Paleo diet
· Take the guesswork out of preparing delicious AND healthy meals for them and their families
· Know exactly what to eat, what to buy, how to make it

Feelings/Messages we want to communicate through the design:
· “Organic” but elegant look
· Fresh/light/Airy
· Simple but NOT GENERIC
· “I want to get cooking” feeling

Our Stylistic preferences:
· Minimalist with a few bold elements (something in between)
· Easy to visually navigate (enough white space, but not too much)
· There is more to “see” than to “read”

Our Color Preferences:
· Lighter pallet
· Colors that evoke natural woods, granite countertops…
· Stay away from using all dark colors

Our Font Type Preferences:
· Easy to read
· Not more than 3 font types
· Not too rigid
· Not too sophisticated
· Simple with a touch

Examples of Website Designs that we like:
· http://www.dorvanta.com/meal-plans/
· http://grulvix.com/
· https://www.mistobarn.com/

```html
<!DOCTYPE html>
<html lang="en">
<head>
<meta charset="utf-8">
<title>Brightwick Supper Kits</title>
<link rel="stylesheet" href="https://fonts.googleapis.com/css2?family=Open+Sans:wght@400;600;700&family=Montserrat:wght@400&display=swap">
<style>
:root{
  --cream:#f7f4ee;
  --ink:#2b2b2b;
  --body:#555;
  --green:#7fae0f;
  --green-dark:#5f8a05;
  --green-light:#93c21b;
  --band:#c6d57a;
  --band-light:#d6e294;
  --orange:#f26a1c;
  --nav-active:#3a3a3a;
  --footer:#2a2a2a;
  --caption:rgba(55,55,55,.82);
}
*{box-sizing:border-box;margin:0;padding:0}
html,body{width:821px;height:1200px;overflow:hidden}
body{position:relative;background:var(--cream);font-family:"Open Sans",Arial,sans-serif;color:var(--ink)}
.abs{position:absolute}

.brand{left:118px;top:24px;display:flex;align-items:center;gap:10px}
.brand-mark{width:22px;height:38px;background:var(--ink)}
.brand-name{font-size:18px;font-weight:400;color:var(--ink);letter-spacing:.1px}

.signup{left:508px;top:34px;width:55px;height:21px;background:var(--green-light);color:#fff;font-size:10px;text-align:center;line-height:21px;border-radius:2px}
.search{left:576px;top:34px;width:128px;height:21px;border:1px solid #cfcfcf;background:#fff;font-size:8px;font-style:italic;color:#999;padding-left:6px;line-height:19px}
.search svg{position:absolute;right:5px;top:4px}

.nav{left:0;top:88px;width:821px;height:34px;background:linear-gradient(#8fbf15,#6f9e07);box-shadow:0 3px 6px rgba(0,0,0,.12)}
.nav-item{position:absolute;top:0;height:34px;line-height:34px;color:#fff;font-size:9.5px;font-weight:600;text-align:center}
.nav-item.active{background:var(--nav-active)}
.nav-sep{position:absolute;top:0;width:1px;height:34px;background:rgba(0,0,0,.12)}
.nav-social{position:absolute;top:97px;width:14px;height:14px;border-radius:50%;background:#fff}

.hero{left:118px;top:145px;width:586px;height:260px;background:linear-gradient(100deg,#b98a52 0%,#e8d2b3 35%,#d8c2a6 60%,#f0e6dc 80%,#c8a57c 100%)}
.caption{left:285px;top:293px;width:252px;height:112px;background:var(--caption);color:#fff;padding:12px 26px}
.caption h2{font-size:17px;font-weight:400;margin-bottom:10px}
.caption p{font-size:8px;line-height:13px;text-align:justify}
.arrow{position:absolute;top:340px;width:26px;height:26px;border-radius:50%;background:rgba(40,40,40,.55)}
.arrow span{position:absolute;left:7px;top:7px;width:12px;height:12px;border-radius:50%;background:#eee}

.welcome{left:0;top:424px;width:821px;text-align:center;font-size:14px;color:var(--ink)}
.welcome em{font-style:normal;color:var(--green-light)}
.intro{left:118px;top:463px;width:586px;text-align:center;font-size:8px;line-height:13px;color:var(--body)}

.band{left:0;top:534px;width:821px;height:170px;background:linear-gradient(90deg,var(--band-light),var(--band) 50%,var(--band-light))}
.band-edge{position:absolute;left:0;width:821px;height:4px;background:radial-gradient(circle at 3px 0,var(--cream) 2.2px,transparent 2.6px) repeat-x;background-size:6px 4px}
.band-title{left:0;top:562px;width:821px;text-align:center;font-size:13.5px;font-weight:600;color:#1e1e1e}
.macro-icon{position:absolute;top:611px;width:58px;height:58px;border-radius:50%;background:#fff}
.macro-icon svg{position:absolute;left:15px;top:15px}
.macro-label{position:absolute;top:611px;font-size:18px;font-weight:600;color:#fff}
.macro-pct{position:absolute;top:637px;font-size:28px;font-weight:600;color:var(--orange)}

.card-img{position:absolute;top:736px;width:180px;height:123px;border:1px solid #ddd;background:#fff;padding:3px}
.card-img div{width:100%;height:100%}
.card-title{position:absolute;top:868px;width:180px;text-align:center;font-size:13px;font-weight:600;color:var(--green-light)}
.card-text{position:absolute;top:898px;width:180px;text-align:center;font-size:7.2px;line-height:12px;color:var(--body)}
.card-btn{position:absolute;top:959px;width:66px;height:23px;border-radius:12px;background:var(--green);color:#fff;font-size:8px;font-weight:600;text-align:center;line-height:23px}

.offer{left:118px;top:1002px;width:586px;height:100px;background:linear-gradient(90deg,#f0f0f0,#e2e2e2)}
.offer-img{left:118px;top:1002px;width:150px;height:100px;background:linear-gradient(90deg,#f4f4f4,#d9d9d9 50%,#f0f0f0)}
.offer h3{position:absolute;left:163px;top:20px;font-size:14px;font-weight:600;color:var(--green)}
.offer p{position:absolute;left:163px;top:58px;width:400px;font-size:8.2px;line-height:13px;color:#444}

.footer{left:0;top:1124px;width:821px;height:76px;background:var(--footer);border-top:2px solid var(--green)}
.footer-links{position:absolute;left:118px;top:17px;font-family:Montserrat,Arial,sans-serif;font-size:7px;color:#ddd;word-spacing:1px}
.copy{position:absolute;left:118px;top:39px;font-family:Montserrat,Arial,sans-serif;font-size:7px;color:#bbb}
.foot-social{position:absolute;top:20px;width:20px;height:20px;border-radius:50%;background:#555;box-shadow:0 1px 2px rgba(0,0,0,.5)}
</style>
</head>
<body>

<div class="abs brand"><span class="brand-mark"></span><span class="brand-name">Brightwick Supper Kits</span></div>
<div class="abs signup">SIGN UP</div>
<div class="abs search">Search
  <svg width="11" height="11" viewBox="0 0 11 11"><circle cx="4.5" cy="4.5" r="3.3" fill="none" stroke="#7fae0f" stroke-width="1.5"/><line x1="7" y1="7" x2="10" y2="10" stroke="#7fae0f" stroke-width="2"/></svg>
</div>

<nav class="abs nav">
  <div class="nav-item active" style="left:118px;width:57px">HOME</div>
  <div class="nav-item" style="left:175px;width:111px">MEAL PLANS</div>
  <div class="nav-sep" style="left:286px"></div>
  <div class="nav-item" style="left:286px;width:75px">ABOUT</div>
  <div class="nav-sep" style="left:361px"></div>
  <div class="nav-item" style="left:361px;width:107px">HOW IT WORKS</div>
  <div class="nav-sep" style="left:468px"></div>
  <div class="nav-item" style="left:468px;width:89px">RESOURCES</div>
  <div class="nav-sep" style="left:557px"></div>
  <div class="nav-item" style="left:557px;width:53px">BLOG</div>
  <div class="nav-sep" style="left:610px"></div>
</nav>
<span class="nav-social" style="left:649px"></span>
<span class="nav-social" style="left:669px"></span>
<span class="nav-social" style="left:689px"></span>

<div class="abs hero" role="img" aria-label="Chef in white hat carefully plating food in a warm kitchen"></div>
<div class="arrow" style="left:272px"><span></span></div>
<div class="arrow" style="left:524px"><span></span></div>
<div class="abs caption">
  <h2>Brightwick Supper Kits</h2>
  <p>Achieve optimal health on the Brightwick Supper Kits diet with weekly meal plans and shopping lists, hundreds of delicious recipes, and super-effective bodyweight workouts you can do from home.</p>
</div>

<h1 class="abs welcome" style="font-weight:400">Welcome To Brightwick <em>Supper Kits</em></h1>
<p class="abs intro">Pellentesque habitant morbi triique senectus et netus et malesuada es ac turpis egestas ersum labilia porc sabliumPellentesque habitant morbi triique senectus et netus et malesuada es ac turpis egestas ersum labilia porc sablium Pellentesque habitant morbi triique senectus et netus et malesuada es ac turpis egestas ersum labilia porc sablium Pellentesque habitant morbi triique senectus et netus et malesuada es ac turpis egestas ersum labilia porc sabliumPellentesque habitant morbi triique senectus et netus et malesuada es ac turpis egestas ersum labilia porc sablium</p>

<section class="abs band">
  <div class="band-edge" style="top:0"></div>
  <div class="band-edge" style="bottom:0;transform:scaleY(-1)"></div>
</section>
<h2 class="abs band-title">We provide membership based program that delivers weekly meal programs</h2>

<div class="macro-icon" style="left:117px"><svg width="28" height="28" viewBox="0 0 28 28"><rect x="2" y="4" width="9" height="20" fill="#111"/><rect x="9" y="14" width="17" height="4" rx="2" fill="#111"/><rect x="9" y="20" width="17" height="4" rx="1" fill="#111"/></svg></div>
<div class="macro-label" style="left:186px">Healthy Fats</div>
<div class="macro-pct" style="left:184px">65%</div>

<div class="macro-icon" style="left:322px"><svg width="28" height="28" viewBox="0 0 28 28"><circle cx="14" cy="16" r="11" fill="#111"/><rect x="13" y="1" width="2" height="6" fill="#111"/></svg></div>
<div class="macro-label" style="left:390px">Lean Protein</div>
<div class="macro-pct" style="left:388px">25%</div>

<div class="macro-icon" style="left:533px"><svg width="28" height="28" viewBox="0 0 28 28"><ellipse cx="14" cy="13" rx="5" ry="11" fill="#111"/><path d="M4 26 L14 16 L24 26 Z" fill="#111"/></svg></div>
<div class="macro-label" style="left:602px">Good Carbs</div>
<div class="macro-pct" style="left:600px">10%</div>

<div class="card-img" style="left:118px"><div role="img" aria-label="Grilled salmon with white asparagus and herbs" style="background:linear-gradient(135deg,#c98c6a,#e7d9c3 55%,#9cae6a)"></div></div>
<h3 class="card-title" style="left:118px">Meal Plans</h3>
<p class="card-text" style="left:118px">Weekly Paleo meal plans—including recipes and shop-ping lists—sent straight to your inbox. No more won-dering what's for dinner.Weekly Paleo meal plans-including recipes and shopping</p>
<div class="card-btn" style="left:170px">Read More</div>

<div class="card-img" style="left:323px"><div role="img" aria-label="Bowl of fresh vegetable salad with meatballs" style="background:linear-gradient(135deg,#a6472a,#d9c879 45%,#8aa84a 70%,#d4a070)"></div></div>
<h3 class="card-title" style="left:323px">QuickStart Guide</h3>
<p class="card-text" style="left:323px">Weekly Paleo meal plans—including recipes and shop-ping lists—sent straight to your inbox. No more won-dering what's for dinner.Weekly Paleo meal plans-including recipes and shopping</p>
<div class="card-btn" style="left:375px">Read More</div>

<div class="card-img" style="left:525px"><div role="img" aria-label="White bowls with tomato, carrot and greens" style="background:linear-gradient(135deg,#e9e6e0,#f4f2ee 40%,#d8533a 70%,#e8e4dc)"></div></div>
<h3 class="card-title" style="left:525px">At-Home Workouts</h3>
<p class="card-text" style="left:525px">Weekly Paleo meal plans—including recipes and shop-ping lists—sent straight to your inbox. No more won-dering what's for dinner.Weekly Paleo meal plans-including recipes and shopping</p>
<div class="card-btn" style="left:577px">Read More</div>

<section class="abs offer">
  <h3>Hot offer! free Brightwick Supper Kits salad</h3>
  <p>Suspendisse tempor sagittis urna. In ut nulla quis erat sagittis commodo a sed felis. Vestibulum aliquam ultricies erat.</p>
</section>
<div class="abs offer-img" role="img" aria-label="Smiling chef in white hat and red scarf holding a plate"></div>

<footer class="abs footer">
  <div class="footer-links">HOME &nbsp; | &nbsp;MEAL PLANS &nbsp;| &nbsp;ABOUT US &nbsp;| &nbsp;RESOURCES &nbsp;| &nbsp;BLOG &nbsp;| &nbsp;CONTACT</div>
  <div class="copy">©2014 Brightwick Supper Kits, All Rights Reserved.</div>
  <span class="foot-social" style="left:602px"></span>
  <span class="foot-social" style="left:628px"></span>
  <span class="foot-social" style="left:655px"></span>
  <span class="foot-social" style="left:682px"></span>
</footer>

</body>
</html>
```